Business cards to launch an education platform

Hi,
I am looking at having new business cards designed.
I am a startup, developing a web platform for schools and university, the education world. It's an online assessment system.
I would like a card that looks classy, and that is using the colors and the font of my logo.

I have attached:
1) my logo
2) A business card that I have designed quickly so you can have all the information required in the card, but I really don't like it.
3) The font that I am using (Lato Regular) to design my web platform
4) Some screenshots of my web platform so you can have a look at the style that I have.

Target Market(s)

Major market: Education system: Schools and university
Minor markets: Business in general

Industry/Entity Type

Business

Contact Information for Business Card

Clara Fenwick
Director

M: 0437 518 902
E: clara.fenwick@amberLoomSystems.com.au

Requirements
Must have
• The colors of my logo

```html
<!DOCTYPE html>
<html lang="en">
<head>
<meta charset="utf-8">
<title>Amber Loom Systems – Business Card</title>
<link href="https://fonts.googleapis.com/css2?family=Lato:wght@300;400;700&display=swap" rel="stylesheet">
<style>
  :root {
    --page-bg: #e8e5e1;
    --navy-deep: #07163a;
    --navy: #0d2a5c;
    --blue-mid: #14477f;
    --blue-bright: #1f7fc4;
    --name-blue: #3f93c6;
    --label-blue: #4a9fd0;
    --text-light: #e4e8ee;
    --text-soft: #c9d2dc;
    --frost: #eef0f1;
    --frost-edge: #d9dde0;
    --brand-ink: #132a4d;
  }
  html, body {
    margin: 0;
    padding: 0;
    width: 1200px;
    height: 969px;
    overflow: hidden;
    background: var(--page-bg);
  }
  .canvas {
    position: relative;
    width: 1200px;
    height: 969px;
  }
  .card {
    position: absolute;
    left: 100px;
    top: 200px;
    width: 1000px;
    height: 568px;
    overflow: hidden;
    background:
      radial-gradient(ellipse 420px 520px at 20% 40%, rgba(20, 71, 127, 0.55), transparent 70%),
      linear-gradient(90deg, var(--blue-mid) 0%, var(--navy) 30%, var(--navy-deep) 62%, var(--navy) 80%, var(--blue-bright) 100%);
    box-shadow: 0 18px 40px rgba(20, 30, 50, 0.22);
  }
  .card__hexagon {
    position: absolute;
    inset: 0;
  }
  .contact {
    position: absolute;
    left: 48px;
    top: 328px;
    font-family: "Lato", sans-serif;
  }
  .contact__name {
    margin: 0;
    font-size: 38px;
    font-weight: 400;
    letter-spacing: 1px;
    color: var(--name-blue);
    text-transform: uppercase;
  }
  .contact__role {
    margin: 8px 0 0;
    font-size: 29px;
    font-weight: 400;
    color: var(--text-soft);
    text-transform: uppercase;
  }
  .contact__line {
    margin: 0;
    font-size: 25px;
    font-weight: 300;
    color: var(--text-light);
  }
  .contact__line--phone { margin-top: 24px; }
  .contact__line--email { margin-top: 6px; }
  .contact__label {
    color: var(--label-blue);
    font-weight: 400;
  }
  .brand {
    position: absolute;
    left: 520px;
    width: 420px;
    top: 150px;
    text-align: center;
    font-family: "Lato", sans-serif;
    font-weight: 400;
    color: var(--brand-ink);
  }
  .brand__square {
    display: block;
    width: 74px;
    height: 74px;
    margin: 0 auto 40px;
    background: var(--brand-ink);
  }
  .brand__name {
    margin: 0;
    font-size: 50px;
    letter-spacing: 4px;
    line-height: 1.05;
    text-transform: uppercase;
  }
  .brand__tagline {
    margin: 4px 0 0;
    font-size: 40px;
    letter-spacing: 2px;
    line-height: 1.05;
  }
</style>
</head>
<body>
<main class="canvas">
  <section class="card" aria-label="Business card">
    <svg class="card__hexagon" width="1000" height="568" viewBox="0 0 1000 568" aria-hidden="true">
      <defs>
        <linearGradient id="frost" x1="0" y1="0" x2="1" y2="1">
          <stop offset="0" stop-color="#f4f5f6"/>
          <stop offset="0.55" stop-color="#e9ecee"/>
          <stop offset="1" stop-color="#d6dbdf"/>
        </linearGradient>
      </defs>
      <polygon points="475,284 570,0 885,0 978,284 885,568 570,568" fill="url(#frost)"/>
    </svg>

    <div class="contact">
      <h1 class="contact__name">Clara Fenwick</h1>
      <p class="contact__role">Director</p>
      <p class="contact__line contact__line--phone"><span class="contact__label">Mobile :</span> 0437 518 902</p>
      <p class="contact__line contact__line--email">clara.fenwick@amberLoomSystems.com.au</p>
    </div>

    <div class="brand">
      <span class="brand__square" aria-hidden="true"></span>
      <p class="brand__name">Amber Loom</p>
      <p class="brand__tagline">Systems</p>
    </div>
  </section>
</main>
</body>
</html>
```